Bright Harbor Web Design & Marketing

Will award a 2nd place prize of $100.00 if someone can come up with a logo to match this design!
Updates

Okay, I'm really looking to see some better designs here. What do you think will bring the best designs out? Please remember with all future submissions I'm looking for a cartoon style / illustrator style website. I'm not sure what the technical term is for it, so I uploaded some images in the brief.

Target Market(s)

Small Business Owners

Industry/Entity Type

Marketing

Logo Text

BrightHarbor.com

Number of Pages Required

1 page

Colors

Designer to choose colors to be used in the design.

Requirements
Must have
• Logo should say BrightHarbor.com I would like more than just a text logo. I want some sort of cool custom graphic / icon with it that will look nice on shirts/hats/etc

```html
<!DOCTYPE html>
<html lang="en">
<head>
<meta charset="utf-8">
<title>Bright Harbor Web Design &amp; Marketing</title>
<link href="https://fonts.googleapis.com/css2?family=Comic+Neue:wght@700&family=Open+Sans:ital,wght@0,400;0,600;0,700;1,400&display=swap" rel="stylesheet">
<style>
:root{
  --blue:#2c67a8;
  --blue-deep:#245a96;
  --sky:#8fcaf3;
  --orange:#f26b2a;
  --orange-dark:#d9551a;
  --ink:#222;
  --muted:#8a8a8a;
  --footer:#2b2b2b;
  --white:#fff;
}
*{margin:0;padding:0;box-sizing:border-box}
html,body{width:1200px;height:3659px;overflow:hidden}
body{font-family:"Open Sans",Arial,sans-serif;color:var(--ink);background:var(--white)}
.page{position:relative;width:1200px;height:3659px;overflow:hidden}
.abs{position:absolute}
.display{font-family:"Comic Neue","Comic Sans MS",cursive;font-weight:700}

/* top bar + nav */
.topbar{left:0;top:0;width:1200px;height:24px;background:var(--orange);color:var(--white);font-size:12px}
.topbar .note{position:absolute;left:200px;top:4px}
.topbar .call{position:absolute;right:200px;top:4px;display:flex;align-items:center;gap:6px}
.nav{left:0;top:24px;width:1200px;height:49px;background:var(--white)}
.brand{position:absolute;left:200px;top:12px;font-weight:700;font-size:24px;color:var(--blue-deep);letter-spacing:.5px}
.menu{position:absolute;right:200px;top:16px;display:flex;gap:30px;list-style:none;font-size:11px;font-weight:700;color:#333}
.menu li.active{color:var(--blue-deep);border-bottom:2px solid var(--orange);padding-bottom:3px}

/* bands */
.band-blue{background:var(--blue);left:0;width:1200px}
.edge{left:0;width:1200px;height:90px}
.edge.to-white{background:linear-gradient(180deg,var(--blue) 0%,var(--sky) 45%,var(--white) 100%)}
.edge.to-blue{background:linear-gradient(180deg,var(--white) 0%,var(--sky) 55%,var(--blue) 100%)}

/* hero */
.hero-title{left:200px;top:185px;width:520px;color:var(--white);font-size:37px;line-height:53px}
.btn{display:flex;align-items:center;justify-content:center;gap:10px;font-weight:600;color:var(--orange);background:var(--white);border:2px solid var(--orange);transform:skewX(-8deg);box-shadow:7px 7px 0 var(--orange);font-size:14px;letter-spacing:.5px}
.btn span,.btn svg{transform:skewX(8deg)}
.hero-btn{left:205px;top:412px;width:248px;height:56px;font-size:16px;letter-spacing:0}
.hero-art{left:640px;top:160px;width:480px;height:430px;border-radius:40px 40px 0 0;background:linear-gradient(160deg,#3d7bc0,#f0a649 85%)}

/* section headings */
.sec-title{left:0;width:1200px;text-align:center;font-size:32px;color:var(--ink)}
.sec-title.light{color:var(--white)}
.sec-title::after{content:"";display:block;width:44px;height:3px;background:var(--orange);margin:6px auto 0}
.tagline{left:0;width:1200px;text-align:center;font-style:italic;font-size:15px;color:#555}
.tagline.light{color:#e6eef8}

/* services */
.services{left:200px;top:800px;width:800px;display:grid;grid-template-columns:repeat(4,1fr);text-align:center}
.service svg{display:block;margin:0 auto 14px;height:62px}
.service h3{font-size:13px;font-weight:600;line-height:17px;color:#333}
.service p{font-size:11px;color:var(--muted);line-height:17px;margin-top:6px}

/* different */
.diff-title{left:200px;top:1290px;color:var(--white);font-size:31px}
.diff-tag{left:200px;top:1343px;color:#e6eef8;font-style:italic;font-size:15px}
.diff-tag::before{content:"";position:absolute;left:0;top:-8px;width:44px;height:3px;background:var(--orange)}
.feature{left:200px;width:470px;display:flex;gap:20px;color:var(--white)}
.feature .ico{width:68px;height:68px;background:var(--white);flex:none;display:flex;align-items:center;justify-content:center}
.feature h4{font-size:14px;font-weight:700;margin-top:2px}
.feature p{font-size:11px;line-height:18px;color:#e6eef8;margin-top:4px}
.diff-art{left:700px;top:1320px;width:380px;height:420px;border-radius:50%;background:radial-gradient(circle at 45% 40%,#4b88c8 0%,#3a78bb 45%,rgba(44,103,168,0) 72%)}

/* about */
.about-art{left:14px;top:1880px;width:170px;height:232px;border-radius:80px 80px 10px 10px;background:linear-gradient(180deg,#f2c89a,#6b6f78 60%)}
.about-text{left:200px;top:1985px;width:800px;text-align:center;font-size:11.5px;line-height:24px;color:#555}
.divider{left:0;top:2281px;width:1200px;border-top:1px dashed #c9c9c9}

/* news */
.news{top:2476px;width:402px;height:195px;background:var(--white);box-shadow:0 4px 14px rgba(0,0,0,.16)}
.news .rule{position:absolute;left:-28px;top:22px;width:100px;height:3px;background:var(--blue)}
.news .date{position:absolute;right:0;top:0;width:60px;height:46px;background:var(--orange);color:var(--white);font-size:11px;font-weight:700;text-align:center;line-height:16px;padding-top:6px}
.news h4{position:absolute;left:112px;top:12px;font-size:14px;font-weight:700}
.news p{position:absolute;left:112px;top:44px;width:250px;font-size:11.5px;line-height:20px;color:#444}
.news .more{position:absolute;left:112px;top:152px;font-size:10px;font-weight:700;display:flex;align-items:center;gap:14px}

/* team */
.member{top:3062px;width:176px;height:251px;background:var(--white)}
.member .photo{position:absolute;left:0;top:0;width:176px;height:210px;background:linear-gradient(180deg,#e8e8e8,#9a9a9a)}
.member .corner{position:absolute;right:0;top:0;width:0;height:0;border-top:20px solid var(--orange);border-left:20px solid transparent}
.member .name{position:absolute;left:0;top:210px;width:176px;height:41px;background:var(--orange);color:var(--white);padding:5px 0 0 14px}
.member .name b{display:block;font-size:11px}
.member .name i{display:block;font-size:10px}
.arrow{width:30px;height:30px;border:2px solid var(--white);border-radius:50%;display:flex;align-items:center;justify-content:center;top:3161px}

/* footer */
.footer{left:0;top:3379px;width:1200px;height:280px;background:var(--footer);color:#eee}
.f-col{top:68px;font-size:11px;line-height:24px}
.f-col h5{font-size:12px;font-weight:700;letter-spacing:.5px;margin-bottom:22px;position:relative}
.f-col h5::before{content:"";position:absolute;left:0;top:-8px;width:40px;height:3px;background:#3d86d6}
.f-col ul{list-style:none}
.socials{display:flex;gap:4px;margin-bottom:10px}
.socials span{width:24px;height:24px;border-radius:3px;background:#3d86d6}
.footer-art{left:1000px;top:73px;width:150px;height:207px;border-radius:70px 70px 0 0;background:linear-gradient(180deg,#f2c89a,#c9d4e0 55%,#e5e5e5)}
</style>
</head>
<body>
<div class="page">
  <div class="abs topbar">
    <span class="note">24/7 U.S. Based Customer Support</span>
    <span class="call"><svg width="12" height="12" viewBox="0 0 24 24"><path fill="#fff" d="M6.6 10.8a15 15 0 0 0 6.6 6.6l2.2-2.2c.3-.3.7-.4 1-.2 1.1.4 2.3.6 3.6.6.6 0 1 .4 1 1V20c0 .6-.4 1-1 1A17 17 0 0 1 3 4c0-.6.4-1 1-1h3.5c.6 0 1 .4 1 1 0 1.3.2 2.5.6 3.6.1.3 0 .7-.2 1z"/></svg>CALL : +1 555 010 2030</span>
  </div>
  <header class="abs nav">
    <div class="brand">BRIGHT HARBOR</div>
    <ul class="menu">
      <li class="active">HOME</li><li>ABOUT US</li><li>SERVICES &amp; PRICING</li><li>OUR TEAM</li><li>PORTFOLIO</li><li>CONTACT US</li>
    </ul>
  </header>

  <!-- hero -->
  <section class="abs band-blue" style="top:73px;height:517px"></section>
  <div class="abs hero-art" role="img" aria-label="Cartoon illustration of two business people meeting at a desk with a laptop"></div>
  <h1 class="abs hero-title display">The Design &amp; MarkeingTeam That Always Puts Trust &amp; Loyalty Before Profits</h1>
  <div class="abs btn hero-btn"><svg width="20" height="20" viewBox="0 0 24 24"><path fill="#f26b2a" d="M6.6 10.8a15 15 0 0 0 6.6 6.6l2.2-2.2c.3-.3.7-.4 1-.2 1.1.4 2.3.6 3.6.6.6 0 1 .4 1 1V20c0 .6-.4 1-1 1A17 17 0 0 1 3 4c0-.6.4-1 1-1h3.5c.6 0 1 .4 1 1 0 1.3.2 2.5.6 3.6.1.3 0 .7-.2 1z"/></svg><span>Contact Us Now</span></div>
  <div class="abs edge to-white" style="top:590px" role="img" aria-label="Decorative cloud border between sections"></div>

  <!-- services -->
  <h2 class="abs sec-title display" style="top:688px">Our Services</h2>
  <p class="abs tagline" style="top:745px">Always Puts Trust &amp; Loyalty Before Profits</p>
  <div class="abs services">
    <div class="service">
      <svg viewBox="0 0 80 62" width="80"><rect x="6" y="8" width="56" height="38" rx="3" fill="#333"/><rect x="10" y="12" width="48" height="30" fill="#cfe3f5"/><rect x="28" y="46" width="12" height="8" fill="#555"/><rect x="20" y="54" width="28" height="4" fill="#333"/><rect x="58" y="22" width="18" height="32" rx="2" fill="#d84a2b"/><rect x="61" y="26" width="12" height="22" fill="#fff"/></svg>
      <h3>Website<br>Design &amp; Management</h3>
      <p>Lorem Ipsum is simply dummy<br>text of the printing</p>
    </div>
    <div class="service">
      <svg viewBox="0 0 62 62" width="62"><circle cx="31" cy="31" r="26" fill="#e03a2b"/><circle cx="31" cy="31" r="17" fill="#fff"/><circle cx="31" cy="31" r="9" fill="#e03a2b"/></svg>
      <h3>Logo Design<br>&amp; Branding Materials</h3>
      <p>Lorem Ipsum is simply dummy<br>text of the printing</p>
    </div>
    <div class="service">
      <svg viewBox="0 0 70 62" width="70"><rect x="6" y="6" width="44" height="32" rx="3" fill="#e9eef3" stroke="#555" stroke-width="2"/><circle cx="30" cy="26" r="14" fill="#fff" stroke="#333" stroke-width="4"/><path d="M40 36 L56 54" stroke="#d84a2b" stroke-width="7" stroke-linecap="round"/></svg>
      <h3>Search<br>Engine Optimization</h3>
      <p>Lorem Ipsum is simply dummy<br>text of the printing</p>
    </div>
    <div class="service">
      <svg viewBox="0 0 62 62" width="62"><circle cx="31" cy="31" r="24" fill="#3b8fd6"/><path d="M31 31 V7 A24 24 0 0 1 55 31 Z" fill="#f26b2a"/><path d="M31 31 H55 A24 24 0 0 1 31 55 Z" fill="#6cc04a"/><circle cx="31" cy="31" r="9" fill="#fff"/></svg>
      <h3>Outsourcing<br>Management</h3>
      <p>Lorem Ipsum is simply dummy<br>text of the printing</p>
    </div>
  </div>
  <div class="abs btn" style="left:510px;top:1010px;width:170px;height:46px"><svg width="18" height="18" viewBox="0 0 24 24"><circle cx="12" cy="12" r="10" fill="#f26b2a"/><path d="M8 12h8M13 8l4 4-4 4" stroke="#fff" stroke-width="2" fill="none"/></svg><span>VIEW MORE</span></div>

  <!-- what makes me different -->
  <div class="abs edge to-blue" style="top:1090px" role="img" aria-label="Decorative cloud border between sections"></div>
  <section class="abs band-blue" style="top:1180px;height:570px"></section>
  <div class="abs diff-art" role="img" aria-label="Illustration of a megaphone surrounded by colourful marketing icon circles"></div>
  <h2 class="abs diff-title display">What makes me different</h2>
  <p class="abs diff-tag">Always Puts Trust &amp; Loyalty Before Profits</p>
  <div class="abs feature" style="top:1400px">
    <div class="ico"><svg width="40" height="40" viewBox="0 0 40 40"><path d="M4 20 A16 16 0 0 1 36 20 Z" fill="#f26b2a"/><path d="M20 20 V32 a3 3 0 0 1 -6 0" stroke="#f26b2a" stroke-width="3" fill="none"/></svg></div>
    <div><h4>100% Risk Free Investment</h4><p>If we are unable to deliver anything that we say we can<br>we will refund you 100% of your investment.</p></div>
  </div>
  <div class="abs feature" style="top:1497px">
    <div class="ico"><svg width="40" height="40" viewBox="0 0 40 40"><rect x="6" y="16" width="28" height="20" fill="#f26b2a"/><rect x="4" y="10" width="32" height="8" fill="#d9551a"/><rect x="18" y="10" width="4" height="26" fill="#fff"/></svg></div>
    <div><h4>Customer Loyalty Program</h4><p>After 12 months of on time payments - Customers will<br>receive cash back reward bonuses .</p></div>
  </div>
  <div class="abs feature" style="top:1594px">
    <div class="ico"><svg width="40" height="40" viewBox="0 0 40 40"><circle cx="20" cy="20" r="16" fill="none" stroke="#f26b2a" stroke-width="3"/><path d="M20 10 V20 L27 24" stroke="#f26b2a" stroke-width="3" fill="none"/></svg></div>
    <div><h4>24/7 U.S. Based Customer Support</h4><p>Phone : +1 555 010 2030<br>E-mail : info@brightharbor.com</p></div>
  </div>
  <div class="abs edge to-white" style="top:1750px" role="img" aria-label="Decorative cloud border between sections"></div>

  <!-- about -->
  <div class="abs about-art" role="img" aria-label="Cartoon businessman presenting with an open hand"></div>
  <h2 class="abs sec-title display" style="top:1880px">About Us</h2>
  <p class="abs tagline" style="top:1945px">Always Puts Trust &amp; Loyalty Before Profits</p>
  <p class="abs about-text">We believe that honesty and integrity come before personal profits. We are a family owned and operated company. Our parents raised us to take care of each other and that's exactly what we've done. We treat each of our clients with the same loyalty and respect that we give each other. We are not looking to have hundreds and hundreds of clients. We are looking to expand our family with a handful of like-minded individuals. Companies who take pride in their work and their customers. We want to build mutually beneficial, lucrative, and long term partnerships.</p>
  <div class="abs btn" style="left:510px;top:2138px;width:210px;height:48px"><svg width="20" height="14" viewBox="0 0 24 16"><path d="M2 8h16M13 3l5 5-5 5M1 3v10" stroke="#f26b2a" stroke-width="2.4" fill="none"/></svg><span>READ MORE</span></div>
  <div class="abs divider"></div>

  <!-- news -->
  <h2 class="abs sec-title display" style="top:2340px">Featured News</h2>
  <p class="abs tagline" style="top:2402px">Always Puts Trust &amp; Loyalty Before Profits</p>
  <article class="abs news" style="left:171px">
    <span class="rule"></span><div class="date">6 Oct<br>2017</div>
    <h4>Lorem Ipsum is Text</h4>
    <p>Lorem Ipsum is simply dummy text of the printing and typesetting industry. Ipsum has been the industry's......</p>
    <div class="more"><svg width="14" height="10" viewBox="0 0 14 10"><path d="M0 5h11M8 1l4 4-4 4" stroke="#f26b2a" stroke-width="2" fill="none"/></svg>READ MORE</div>
  </article>
  <article class="abs news" style="left:598px">
    <span class="rule"></span><div class="date">6 Oct<br>2017</div>
    <h4>Lorem Ipsum is Text</h4>
    <p>Lorem Ipsum is simply dummy text of the printing and typesetting industry. Ipsum has been the industry's......</p>
    <div class="more"><svg width="14" height="10" viewBox="0 0 14 10"><path d="M0 5h11M8 1l4 4-4 4" stroke="#f26b2a" stroke-width="2" fill="none"/></svg>READ MORE</div>
  </article>
  <div class="abs btn" style="left:510px;top:2712px;width:170px;height:46px"><svg width="16" height="18" viewBox="0 0 16 18"><rect x="1" y="1" width="14" height="16" fill="#f26b2a"/><path d="M4 6h8M4 10h8M4 14h5" stroke="#fff" stroke-width="1.6"/></svg><span>VIEW MORE</span></div>

  <!-- team -->
  <div class="abs edge to-blue" style="top:2812px" role="img" aria-label="Decorative cloud border between sections"></div>
  <section class="abs band-blue" style="top:2902px;height:478px"></section>
  <h2 class="abs sec-title light display" style="top:2938px">Our Team</h2>
  <p class="abs tagline light" style="top:3000px">Always Puts Trust &amp; Loyalty Before Profits</p>
  <div class="abs arrow" style="left:58px"><svg width="12" height="12" viewBox="0 0 12 12"><path d="M8 1L3 6l5 5" stroke="#fff" stroke-width="2" fill="none"/></svg></div>
  <div class="abs arrow" style="left:1102px"><svg width="12" height="12" viewBox="0 0 12 12"><path d="M4 1l5 5-5 5" stroke="#fff" stroke-width="2" fill="none"/></svg></div>
  <div class="abs member" style="left:202px"><div class="photo" role="img" aria-label="Portrait photo of a team member"></div><span class="corner"></span><div class="name"><b>JEMS SMITH</b><i>Chief Executive Officer</i></div></div>
  <div class="abs member" style="left:405px"><div class="photo" role="img" aria-label="Portrait photo of a team member"></div><span class="corner"></span><div class="name"><b>JOHN DOE</b><i>Chief Operations Officer</i></div></div>
  <div class="abs member" style="left:610px"><div class="photo" role="img" aria-label="Portrait photo of a team member"></div><span class="corner"></span><div class="name"><b>JEMS SMITH</b><i>Chief Technical Officer</i></div></div>
  <div class="abs member" style="left:815px"><div class="photo" role="img" aria-label="Portrait photo of a team member"></div><span class="corner"></span><div class="name"><b>JOHN DOE</b><i>Finance Officer</i></div></div>

  <!-- footer -->
  <footer class="abs footer">
    <div class="abs f-col" style="left:200px;width:340px">
      <h5>PERSONAL SERVICE</h5>
      <p>Do you need us to come to your office to help train staff on the management of your new website, content management system, or computer software? That's not a problem. We will come to you and provide hands on training.</p>
      <p style="margin-top:12px">E-mail : info@brightharbor.com</p>
    </div>
    <div class="abs f-col" style="left:585px">
      <h5>COMPANY LINKS</h5>
      <ul><li>Home</li><li>About Us</li><li>Services &amp; Pricing</li><li>Our Team</li><li>Portfolio</li><li>Contact Us</li></ul>
    </div>
    <div class="abs f-col" style="left:768px">
      <h5>SOCIAL ICONS</h5>
      <div class="socials"><span></span><span></span><span></span><span></span></div>
      <p>© 2017 brightharbor. All Rights Reserved<br>Privacy Policy.</p>
    </div>
    <div class="abs footer-art" role="img" aria-label="Cartoon man with glasses and a tie"></div>
  </footer>
</div>
</body>
</html>
```